Harborview Estates Business Card for Apartment Buildings

Create business cards for resident managers who run apartment buildings. The audience is the public who are searching for apartment rentals, and current residents who live at the apartment building. Key design element will be incorporating the company logo, however, the logo cannot dominate. The building name and manager name are more important than the logo. Current business card design leaves little room for copy, so we may need to reduce the size on the current card to allow for more space for copy.

Target Market(s)

Adults 18-65 years of age, who are looking for an apartment rental, plus current residents who live at our apartment buildings.

Industry/Entity Type

Property Management

Contact Information for Business Card

A major design element will be use of the company logo. Important property and manager contact information must be part of the design. The size of the logo will need to be reduced to make room for building and manager contact copy.

Font styles to use
Sans Serif

Colors
3176b5
000000
959595
ffffff

Requirements
Must have
• 1) Incorporate the company logo.
• 2) Use the company colors (dark blue, black/grey, over white).
• 3) FEATURE THE BUILDING NAME
• 4) FEATURE THE MANAGER NAME
• 5) The company name is less important than BUILDING and MANAGER
• 6) Manager contact information
• **SEE ATTACHED CREATIVE BRIEF**
Nice to have
• 1) Back of card logo watermark
• 2) Ability to write notes on back of carfd
Should not have
• Avoid letting the company logo dominate the card, the building name and manager are more important than the company logo.

```html
<!DOCTYPE html>
<html lang="en">
<head>
<meta charset="utf-8">
<title>Harborview Estates – Resident Manager Business Card</title>
<link rel="stylesheet" href="https://fonts.googleapis.com/css2?family=Hind:wght@600&family=Roboto:wght@400&family=Roboto+Condensed:wght@700&display=swap">
<style>
  :root {
    --brand-blue: #0f68a4;
    --brand-blue-deep: #0c5d95;
    --charcoal: #414143;
    --paper: #f2f2f2;
    --white: #ffffff;
    --backdrop: #262626;
    --grey-mark: #4a4a4c;
  }
  * { margin: 0; padding: 0; box-sizing: border-box; }
  html, body {
    width: 1200px; height: 960px; overflow: hidden;
    background: var(--backdrop);
  }
  .card {
    position: absolute;
    width: 600px; height: 342px;
    box-shadow: 0 3px 8px rgba(0,0,0,.55);
    overflow: hidden;
  }
  .card--front {
    left: 314px; top: 113px;
    background: linear-gradient(180deg, var(--brand-blue) 0%, var(--brand-blue-deep) 100%);
    color: var(--white);
  }
  .card--back { left: 311px; top: 472px; background: var(--paper); }

  .front-panel { position: absolute; inset: 0; }

  .manager { position: absolute; left: 36px; top: 46px; font-family: "Hind", sans-serif; font-weight: 600; }
  .manager__name { font-size: 23px; letter-spacing: .5px; line-height: 1; text-transform: uppercase; }
  .manager__title { font-size: 15px; letter-spacing: .6px; line-height: 1; margin-top: 6px; text-transform: uppercase; }

  .property { position: absolute; left: 36px; top: 130px; font-family: "Roboto", sans-serif; }
  .property__name { font-family: "Roboto Condensed", sans-serif; font-weight: 700; font-size: 21px; line-height: 1; margin-bottom: 6px; }
  .property__address { font-size: 14px; line-height: 18px; }

  .contact { position: absolute; left: 36px; top: 209px; list-style: none; font-family: "Roboto", sans-serif; font-size: 14px; }
  .contact li { display: flex; align-items: center; height: 19px; }
  .contact svg { width: 13px; height: 13px; margin-right: 10px; fill: var(--white); flex: none; }

  .brand {
    position: absolute; left: 0; right: 0; top: 150px;
    display: flex; justify-content: center; align-items: center; gap: 14px;
  }
  .brand__dot { width: 30px; height: 30px; border-radius: 50%; background: var(--grey-mark); }
  .brand__name {
    font-family: "Roboto Condensed", sans-serif; font-weight: 700;
    font-size: 34px; letter-spacing: 1px; color: var(--brand-blue); text-transform: uppercase;
  }
</style>
</head>
<body>
  <section class="card card--front">
    <svg class="front-panel" width="600" height="342" viewBox="0 0 600 342" role="img" aria-label="Dark grey decorative panel where the company emblem sits">
      <circle cx="462" cy="176" r="176" fill="var(--charcoal)"/>
      <rect x="462" y="0" width="138" height="342" fill="var(--charcoal)"/>
    </svg>

    <div class="manager">
      <p class="manager__name">Marisol Delgado</p>
      <p class="manager__title">Resident Manager</p>
    </div>

    <div class="property">
      <p class="property__name">Cedar Court Apartments</p>
      <p class="property__address">1824 Linden Avenue<br>Bayport, CA 90417</p>
    </div>

    <ul class="contact">
      <li><svg viewBox="0 0 16 16"><path d="M3.5 1l2.5 3-1.5 2c1 2 3 4 5 5l2-1.5 3 2.5-1.5 2.5C7 16 0 9 1 2.5z"/></svg>555-214-3080</li>
      <li><svg viewBox="0 0 16 16"><path d="M4 0h8v16H4zM5.5 2v10h5V2zM7 13.3h2v1.4H7z" fill-rule="evenodd"/></svg>555-386-7142</li>
      <li><svg viewBox="0 0 16 16"><path d="M4 1h8v4H4zM1 6h14v6h-2v3H3v-3H1zM4.5 10v3.5h7V10z" fill-rule="evenodd"/></svg>555-490-6615</li>
      <li><svg viewBox="0 0 16 16"><path d="M1 3h14v1L8 9 1 4zM1 5.5l7 5 7-5V13H1z"/></svg>marisol@harborviewest.com</li>
      <li><svg viewBox="0 0 16 16"><path d="M8 1a7 7 0 1 0 0 14A7 7 0 0 0 8 1zM4 5c1.5-.5 2.5.5 2 2s1 2 1.5 3.5-1 2.5-2 2.5C3.5 12 3 8 4 5zm6-2c1.5.5 3 2 3 4-1 0-2-.5-2.5.5S10 10 9.5 9 8 5 10 3z" fill-rule="evenodd"/></svg>www.harborviewest.com</li>
    </ul>
  </section>

  <section class="card card--back">
    <div class="brand">
      <span class="brand__dot"></span>
      <span class="brand__name">Harborview Estates</span>
    </div>
  </section>
</body>
</html>
```